LoopVane - A ride hailing server VAR

our Brindle.co profile: https://brindle.co/517loopvane

LOOPVANE offers first world solutions to first world problems. These days, our smartphones are our cameras, our wallets and our ride home. LOOPVANE guarantees that even if your phone is lost or dies, you'll never get stranded again. Simply call or text (SMS) our toll-free number to request a ride, and choose from one of the various services you subscribe to. LOOPVANE verifies your identity through a unique pin, making it possible to request rides through your own account from a stranger's phone via text or phone call. You can also login through our website or our App, making it easier than ever to get home phoneless.

LOOPVANE is a heterogeneous ride-hailing service that allows users for request transportation from any "transportation network company," taxi, helicopter service, jet service or any transportation service company that is publicly available. LOOPVANE will allow users to connect through our site, automated phone system, App or any appropriated touch point available.

Target Market(s)

RIde Haling

Coding

Coded - Design and coding required

Number of Pages Required

4 page

Requirements
Must have
• hav
Nice to have
• e the same functionality as our competitor's site: https://hopquill.com/
Should not have
• should not be cheezy
• We need to have the registration/sign up on the main page like https://www.zarvix.com/

```html
<!DOCTYPE html>
<html lang="en">
<head>
<meta charset="utf-8">
<title>LoopVane – Support</title>
<link href="https://fonts.googleapis.com/css2?family=Open+Sans:wght@400;600;700&display=swap" rel="stylesheet">
<style>
:root{
  --accent:#f5a300;
  --accent-soft:#f7b21f;
  --ink:#222;
  --text:#444;
  --muted:#777;
  --line:#d9d9d9;
  --nav:#4a4a4a;
  --footer:#121212;
  --white:#fff;
}
*{box-sizing:border-box;margin:0;padding:0}
html,body{width:1145px;height:1200px;overflow:hidden}
body{font-family:"Open Sans",Arial,sans-serif;color:var(--text);background:var(--white);position:relative}
.site-header{height:99px;position:relative}
.brand{position:absolute;left:85px;top:20px;display:flex;align-items:center;gap:9px}
.brand-mark{width:55px;height:55px;background:var(--accent);border-radius:7px}
.brand-name{font-size:21px;font-weight:700;color:var(--ink);letter-spacing:.3px}
.service-cars{position:absolute;right:92px;top:29px;display:flex;gap:10px}
.service-car{width:95px;height:37px;border-radius:8px;background:linear-gradient(180deg,var(--accent-soft),var(--accent))}
.main-nav{height:55px;background:var(--nav);position:relative}
.main-nav a{position:absolute;top:0;height:55px;line-height:55px;color:var(--white);font-size:13px;text-decoration:none;transform:translateX(-50%)}
.main-nav a.is-active::after{content:"";position:absolute;left:0;right:0;bottom:0;height:4px;background:var(--accent)}
.page-title{position:absolute;top:194px;width:100%;text-align:center;font-size:25px;font-weight:400;color:var(--ink);letter-spacing:.5px}
.title-rule{position:absolute;left:85px;width:976px;top:246px;border-top:1px solid var(--line)}
.search{position:absolute;left:110px;top:266px;width:929px;height:46px;border:1px solid var(--line);box-shadow:0 1px 2px rgba(0,0,0,.08);display:flex;align-items:center;padding:0 19px;font-size:14px;color:var(--text);justify-content:space-between}
.filters{position:absolute;left:112px;top:330px;font-size:15px;color:var(--muted);display:flex;gap:19px}
.filters .is-current{color:var(--accent);margin-left:-7px}
.sort{position:absolute;left:949px;top:325px;width:90px;height:33px;border:1px solid var(--line);font-size:13px;color:var(--text);display:flex;align-items:center;padding-left:12px;gap:14px}
.sort::after{content:"";border:4px solid transparent;border-top:5px solid var(--ink);margin-top:5px}
.question{position:absolute;left:109px;width:930px;height:77px;border:1px solid var(--line);box-shadow:0 1px 3px rgba(0,0,0,.1);background:var(--white)}
.question .avatar{position:absolute;left:19px;top:15px;width:43px;height:43px;background:var(--accent);border-radius:6px}
.question h2{position:absolute;left:73px;top:16px;font-size:14px;font-weight:400;color:var(--text)}
.question .meta{position:absolute;left:73px;top:40px;font-size:12px;color:var(--text)}
.meta .status,.meta .tags{color:var(--accent)}
.stats{position:absolute;right:16px;top:13px;display:flex;gap:9px}
.stat{width:51px;height:49px;border:1px solid var(--line);text-align:center;font-size:11px;line-height:16px;padding-top:8px;color:var(--text)}
.stat.wide{width:54px}
.pager{position:absolute;left:107px;top:832px;display:flex;gap:9px}
.pager span{height:26px;min-width:26px;padding:0 11px;border:1px solid var(--line);font-size:13px;line-height:24px;text-align:center;color:var(--muted)}
.pager .is-current{background:var(--nav);color:var(--white);border-color:var(--nav);padding:0 9px}
.ask{position:absolute;left:939px;top:828px;width:98px;height:33px;border:1px solid var(--line);font-size:13px;line-height:31px;text-align:center;color:var(--text)}
.site-footer{position:absolute;left:0;top:909px;width:1145px;height:291px;background:var(--footer);color:var(--white);font-size:12px}
.foot-col{position:absolute;top:38px;list-style:none}
.foot-col li{height:34.4px}
.foot-col.locale li{display:flex;gap:6px;align-items:flex-start}
.foot-col svg{margin-top:2px}
.social{position:absolute;left:87px;top:180px;display:flex;gap:13px}
.social span{width:10px;height:10px;border-radius:50%;background:var(--white)}
.store-badges{position:absolute;left:857px;top:51px;display:flex;gap:12px}
.store-badges span{width:98px;height:28px;border:1px solid #888;border-radius:4px;background:#000}
.store-badges span+span{width:90px}
.foot-rule{position:absolute;left:85px;width:976px;top:226px;border-top:1px solid #444}
.copyright{position:absolute;top:250px;width:100%;text-align:center;font-size:12px}
</style>
</head>
<body>
<header class="site-header">
  <div class="brand"><span class="brand-mark"></span><span class="brand-name">LOOPVANE</span></div>
  <div class="service-cars">
    <div class="service-car" role="img" aria-label="Car illustration for the first partner ride service"></div>
    <div class="service-car" role="img" aria-label="Car illustration for the second partner ride service"></div>
    <div class="service-car" role="img" aria-label="Taxi car illustration"></div>
  </div>
</header>
<nav class="main-nav">
  <a style="left:169px">HOME</a><a style="left:319px">ABOUT</a><a style="left:474px">SIGN UP</a><a style="left:631px">SIGN IN</a><a class="is-active" style="left:791px">SUPPORT</a><a style="left:956px">CONTACT</a>
</nav>
<main>
  <h1 class="page-title">SUPPORT</h1>
  <div class="title-rule"></div>
  <div class="search"><span>What do you want to know?</span>
    <svg width="14" height="14" viewBox="0 0 14 14"><circle cx="6" cy="6" r="4.5" fill="none" stroke="#555" stroke-width="2"/><line x1="9.3" y1="9.3" x2="13" y2="13" stroke="#555" stroke-width="2.2"/></svg></div>
  <div class="filters"><span>Filter :</span><span class="is-current">All</span><span>Open</span><span>Resolved</span><span>Closed</span><span>Unanswered</span></div>
  <div class="sort">Sort by</div>

  <article class="question" style="top:378px"><span class="avatar"></span><h2>How do I request a ride by SMS?</h2><p class="meta"><span class="status">open</span>&nbsp;&nbsp; loopvane asked 1 month ago • <span class="tags">Phone, SMS</span></p>
    <div class="stats"><div class="stat">17<br>views</div><div class="stat wide">0<br>answers</div><div class="stat">0<br>votes</div></div></article>
  <article class="question" style="top:467px"><span class="avatar"></span><h2>Does HopQuill support requesting rides with Drivo by calling/dialing?</h2><p class="meta"><span class="status">open</span>&nbsp;&nbsp; loopvane asked 1 month ago • <span class="tags">Phone, SMS</span></p>
    <div class="stats"><div class="stat">56<br>views</div><div class="stat wide">1<br>answers</div><div class="stat">0<br>votes</div></div></article>
  <article class="question" style="top:556px"><span class="avatar"></span><h2>How do I sign up?</h2><p class="meta"><span class="status">open</span>&nbsp;&nbsp; loopvane asked 1 month ago • <span class="tags">Phone, SMS</span></p>
    <div class="stats"><div class="stat">26<br>views</div><div class="stat wide">0<br>answers</div><div class="stat">1<br>votes</div></div></article>
  <article class="question" style="top:644px"><span class="avatar"></span><h2>How do I add a new rider and choose a PIN?</h2><p class="meta"><span class="status">open</span>&nbsp;&nbsp; loopvane asked 1 month ago • <span class="tags">Phone, SMS</span></p>
    <div class="stats"><div class="stat">85<br>views</div><div class="stat wide">1<br>answers</div><div class="stat">0<br>votes</div></div></article>
  <article class="question" style="top:732px"><span class="avatar"></span><h2>How do I request a ride by calling?</h2><p class="meta"><span class="status">open</span>&nbsp;&nbsp; loopvane asked 1 month ago • <span class="tags">Phone, SMS</span></p>
    <div class="stats"><div class="stat">25<br>views</div><div class="stat wide">0<br>answers</div><div class="stat">0<br>votes</div></div></article>

  <div class="pager"><span class="is-current">1</span><span>2</span><span>...</span><span>Next</span></div>
  <div class="ask">Ask Question</div>
</main>
<footer class="site-footer">
  <ul class="foot-col locale" style="left:86px">
    <li><svg width="8" height="11" viewBox="0 0 8 11"><path d="M4 0a4 4 0 0 1 4 4c0 3-4 7-4 7S0 7 0 4a4 4 0 0 1 4-4z" fill="#fff"/><circle cx="4" cy="4" r="1.5" fill="#121212"/></svg>Enter Your Location</li>
    <li><svg width="11" height="11" viewBox="0 0 11 11"><circle cx="5.5" cy="5.5" r="5.5" fill="#fff"/><path d="M3 3l2 1v2l-1 2M7 2l1 3 2 1" stroke="#121212" fill="none"/></svg>ENGLISH</li>
    <li><svg width="12" height="12" viewBox="0 0 12 12"><circle cx="6" cy="6" r="5" fill="none" stroke="#fff" stroke-width="2"/><circle cx="6" cy="6" r="2" fill="none" stroke="#fff" stroke-width="1.5"/></svg>Help</li>
  </ul>
  <ul class="foot-col" style="left:387px"><li>Ride</li><li>Drive</li><li>Cities</li><li>Fare Estimate</li><li>How it Works</li></ul>
  <ul class="foot-col" style="left:668px;top:37px"><li>Safety</li><li>Careers</li><li>Helping Cities</li><li>Our Story</li><li>Newsroom</li></ul>
  <div class="store-badges"><span></span><span></span></div>
  <div class="social"><span></span><span></span><span></span><span></span></div>
  <div class="foot-rule"></div>
  <p class="copyright">Copyright © 2017. All Rights Reserved</p>
</footer>
</body>
</html>
```